BOLD & MINIMALIST DESIGN NEEDED

We want a very bold but minimalistic business card design that is impactful and utilizes both sides of the business card. Our current logo is included for your use.

We want bold fonts and good use of negative space. We don't want the logo to overpower the design.

Target Market(s)

Professionals who are building new commercial buildings.

Industry/Entity Type

Construction

Contact Information for Business Card

Name, Title, email, office phone, cell phone, website

Font styles to use
Serif
Sans Serif

Requirements
Must have
• Bold design!

```html
<!DOCTYPE html>
<html lang="en">
<head>
<meta charset="utf-8">
<title>Ridgeline Design + Build — Business Card</title>
<link href="https://fonts.googleapis.com/css2?family=Montserrat:wght@400;500;600;800&display=swap" rel="stylesheet">
<style>
  :root {
    --stage: #3a3a3a;
    --card: #1f1f1f;
    --card-edge: #2a2a2a;
    --green: #7dc242;
    --white: #f4f4f4;
    --emboss: #2d2d2d;
    --muted: #bdbdbd;
  }
  * { box-sizing: border-box; margin: 0; padding: 0; }
  html, body {
    width: 1200px; height: 875px; overflow: hidden;
    background: var(--stage);
    font-family: "Montserrat", Arial, sans-serif;
  }
  .stage {
    width: 1200px; height: 875px;
    display: flex; align-items: center; justify-content: center; gap: 36px;
  }
  .card {
    position: relative;
    width: 560px; height: 320px;
    background: var(--card);
    border-radius: 18px;
    border: 1px solid var(--card-edge);
    box-shadow: 0 18px 40px rgba(0,0,0,.45);
    overflow: hidden;
  }
  /* Front */
  .card--front { display: flex; align-items: center; justify-content: center; }
  .brand {
    display: flex; align-items: center; gap: 12px;
  }
  .brand__mark { width: 18px; height: 18px; background: currentColor; }
  .brand__name {
    font-weight: 800; letter-spacing: .02em; line-height: 1.05;
    text-transform: uppercase;
  }
  .card--front .brand { color: var(--emboss); }
  .card--front .brand__name { font-size: 38px; }
  .card--front .brand__mark { width: 26px; height: 26px; }

  /* Back */
  .holder {
    position: absolute; top: 30px; right: 40px; text-align: right;
  }
  .holder__name {
    color: var(--green); font-weight: 800; font-size: 26px; letter-spacing: .02em;
  }
  .holder__title {
    color: var(--white); font-weight: 500; font-size: 14px; margin-top: 2px;
  }
  .accent-bar {
    position: absolute; top: 30px; right: 0; width: 14px; height: 34px;
    background: var(--green);
  }
  .card--back .brand {
    position: absolute; left: 44px; top: 120px; color: var(--white);
  }
  .card--back .brand__name { font-size: 26px; }
  .contacts {
    position: absolute; left: 44px; bottom: 30px;
    list-style: none; display: grid; gap: 6px;
    color: var(--white); font-size: 14px; font-weight: 500;
  }
  .contacts li { display: flex; align-items: center; gap: 9px; }
  .contacts svg { width: 13px; height: 13px; flex: none; }
  .contacts .hl { color: var(--green); }
</style>
</head>
<body>
<main class="stage">
  <section class="card card--front" aria-label="Card front">
    <div class="brand">
      <span class="brand__mark"></span>
      <span class="brand__name">Ridgeline<br>Design + Build</span>
    </div>
  </section>

  <section class="card card--back" aria-label="Card back">
    <div class="accent-bar"></div>
    <div class="holder">
      <p class="holder__name">DANIEL REEVES</p>
      <p class="holder__title">Owner/CEO</p>
    </div>

    <div class="brand">
      <span class="brand__mark"></span>
      <span class="brand__name">Ridgeline<br>Design + Build</span>
    </div>

    <ul class="contacts">
      <li>
        <svg viewBox="0 0 24 24" fill="var(--green)"><path d="M6.6 10.8a15.1 15.1 0 0 0 6.6 6.6l2.2-2.2a1 1 0 0 1 1-.25 11.4 11.4 0 0 0 3.6.57 1 1 0 0 1 1 1V20a1 1 0 0 1-1 1A17 17 0 0 1 3 4a1 1 0 0 1 1-1h3.5a1 1 0 0 1 1 1c0 1.25.2 2.45.57 3.6a1 1 0 0 1-.25 1z"/></svg>
        07 5120 4400
      </li>
      <li>
        <svg viewBox="0 0 24 24" fill="none" stroke="var(--green)" stroke-width="2.4"><rect x="6" y="2" width="12" height="20" rx="2"/><line x1="11" y1="18" x2="13" y2="18"/></svg>
        0412 555 019
      </li>
      <li>
        <svg viewBox="0 0 24 24" fill="var(--green)"><path d="M2 5h20v14H2z"/><path d="M2 5l10 8 10-8" fill="none" stroke="var(--card)" stroke-width="2"/></svg>
        info@ridgelinebuild.com
      </li>
      <li>
        <svg viewBox="0 0 24 24" fill="none" stroke="var(--green)" stroke-width="2.2"><circle cx="12" cy="12" r="10"/><path d="M2 12h20M12 2a15 15 0 0 1 0 20M12 2a15 15 0 0 0 0 20"/></svg>
        <span>www.<span class="hl">ridgelinebuild</span>.com</span>
      </li>
    </ul>
  </section>
</main>
</body>
</html>
```